Corvane Paintless Dent Removal

Our company works on vehicles removing dents using a highly skilled trade which the metal is massaged out with special tools without disturbing the original paint, hence paintless dent removal. Besides keeping the paint and metal original its also very environmentally friendly since no paint or toxic fillers are used. Also we we are one of the most experienced companies in the business with 25 years

Target Market(s)

Retail Automobile consumers, Auto Dealerships and Auto Body Shops

Industry/Entity Type

Auto Repair

Contact Information for Business Card

Dale Hollister
PO Box 518 Brookmere, NY 11962
631-555-0148
corvanepdr@mailbox-example.com
website corvanepdr.example
youtube corvane paintless dent removal
25 years of experience removing Dents, Dings and Hail Damage

Font styles to use
Serif
Sans Serif

Colors

Designer to choose colors to be used in the design.

Requirements
Must have
• I do like things that are simple but classy and somewhat bold, also I like my logo so that should be somewhat important

```html
<!DOCTYPE html>
<html lang="en">
<head>
<meta charset="utf-8">
<title>Corvane Paintless Dent Removal – Business Card</title>
<link href="https://fonts.googleapis.com/css2?family=Roboto:wght@400;500;700;900&display=swap" rel="stylesheet">
<style>
  :root {
    --navy: #13294b;
    --green: #76b814;
    --green-light: #8cc63f;
    --white: #ffffff;
    --card-white: #f7f7f6;
    --text-grey: #555a60;
    --rule-grey: #9a9a9a;
    --gold: #d9a53a;
    --backdrop: #e6e3df;
  }
  html, body {
    margin: 0;
    padding: 0;
    width: 1200px;
    height: 960px;
    overflow: hidden;
    background: var(--backdrop);
    font-family: "Roboto", Arial, sans-serif;
  }
  .canvas {
    position: relative;
    width: 1200px;
    height: 960px;
  }
  .card {
    position: absolute;
    width: 600px;
    height: 342px;
    overflow: hidden;
    box-shadow: 0 4px 10px rgba(0,0,0,0.18);
  }
  .card-front {
    left: 314px;
    top: 113px;
    background: var(--card-white);
  }
  .card-back {
    left: 311px;
    top: 472px;
    background: var(--green);
  }

  /* front */
  .brand-name {
    position: absolute;
    left: 34px;
    top: 142px;
    width: 246px;
    text-align: center;
    color: var(--navy);
    font-weight: 900;
    line-height: 1;
    margin: 0;
  }
  .brand-name .word-main {
    display: block;
    font-size: 36px;
    letter-spacing: -0.5px;
    text-transform: uppercase;
  }
  .brand-name .word-sub {
    display: block;
    font-size: 13.5px;
    margin-top: 4px;
  }
  .divider {
    position: absolute;
    left: 303px;
    top: 100px;
    width: 1px;
    height: 132px;
    background: var(--rule-grey);
  }
  .contact {
    position: absolute;
    left: 327px;
    top: 98px;
    color: var(--text-grey);
    font-size: 14px;
    line-height: 18px;
  }
  .contact-name {
    margin: 0 0 11px;
    color: var(--navy);
    font-size: 20px;
    font-weight: 500;
    text-transform: uppercase;
    letter-spacing: 0.2px;
  }
  .contact-address {
    margin: 0 0 8px;
    font-style: normal;
  }
  .contact-list {
    list-style: none;
    margin: 0;
    padding: 0;
  }
  .contact-list li {
    display: flex;
    align-items: center;
    height: 19px;
  }
  .contact-icon {
    width: 13px;
    height: 13px;
    margin-right: 9px;
    flex: none;
  }
  .experience-seal {
    position: absolute;
    left: 505px;
    top: 18px;
    width: 72px;
    height: 72px;
    border-radius: 50%;
    background: var(--gold);
  }
  .front-swoosh {
    position: absolute;
    left: 0;
    bottom: 0;
    width: 600px;
    height: 60px;
  }
  .front-web {
    position: absolute;
    left: 0;
    right: 0;
    bottom: 10px;
    text-align: center;
    color: var(--white);
    font-size: 13px;
    letter-spacing: 3.6px;
  }

  /* back */
  .back-brand {
    position: absolute;
    left: 0;
    right: 0;
    top: 138px;
    text-align: center;
    color: var(--white);
    font-weight: 900;
    line-height: 1;
    margin: 0;
  }
  .back-brand .word-main {
    display: block;
    font-size: 38px;
    text-transform: uppercase;
    letter-spacing: -0.5px;
  }
  .back-brand .word-sub {
    display: block;
    font-size: 14px;
    margin-top: 5px;
  }
  .back-web {
    position: absolute;
    left: 0;
    right: 0;
    top: 280px;
    text-align: center;
    color: var(--white);
    font-size: 13px;
    letter-spacing: 5.2px;
  }
</style>
</head>
<body>
<main class="canvas">

  <section class="card card-front" aria-label="Business card front">
    <span class="experience-seal" aria-hidden="true"></span>

    <h1 class="brand-name">
      <span class="word-main">Corvane</span>
      <span class="word-sub">Paintless Dent Removal</span>
    </h1>

    <span class="divider" aria-hidden="true"></span>

    <div class="contact">
      <p class="contact-name">Dale Hollister</p>
      <address class="contact-address">PO Box 518<br>Brookmere, NY 11962</address>
      <ul class="contact-list">
        <li>
          <svg class="contact-icon" viewBox="0 0 24 24" aria-hidden="true"><path fill="#13294b" d="M6.6 10.8a15.1 15.1 0 0 0 6.6 6.6l2.2-2.2a1 1 0 0 1 1-.25 11.4 11.4 0 0 0 3.6.57 1 1 0 0 1 1 1V20a1 1 0 0 1-1 1A17 17 0 0 1 3 4a1 1 0 0 1 1-1h3.5a1 1 0 0 1 1 1c0 1.25.2 2.45.57 3.57a1 1 0 0 1-.25 1z"/></svg>
          631-555-0148
        </li>
        <li>
          <svg class="contact-icon" viewBox="0 0 24 24" aria-hidden="true"><path fill="#13294b" d="M3 5h18a1 1 0 0 1 1 1v12a1 1 0 0 1-1 1H3a1 1 0 0 1-1-1V6a1 1 0 0 1 1-1zm1 2.2V17h16V7.2l-8 5.3z M4.5 7l7.5 5 7.5-5z"/></svg>
          corvanepdr@mailbox-example.com
        </li>
        <li>
          <svg class="contact-icon" viewBox="0 0 24 24" aria-hidden="true"><rect x="2" y="5" width="20" height="14" rx="3" fill="#13294b"/></svg>
          corvane paintless dent removal
        </li>
      </ul>
    </div>

    <svg class="front-swoosh" viewBox="0 0 600 60" preserveAspectRatio="none" aria-hidden="true">
      <path d="M0 46 Q 250 -8 600 40 L600 60 L0 60 Z" fill="#8cc63f"/>
      <path d="M0 54 Q 250 -4 600 36 L600 60 L0 60 Z" fill="#ffffff"/>
      <path d="M0 58 Q 250 0 600 39 L600 60 L0 60 Z" fill="#13294b"/>
    </svg>
    <p class="front-web" style="margin:0">www.corvanepdr.example</p>
  </section>

  <section class="card card-back" aria-label="Business card back">
    <h2 class="back-brand">
      <span class="word-main">Corvane</span>
      <span class="word-sub">Paintless Dent Removal</span>
    </h2>
    <p class="back-web" style="margin:0">www.corvanepdr.example</p>
  </section>

</main>
</body>
</html>
```